Marrowby Water Taxi and Transport Business Card

I need business cards for my new water taxi and freight transport business I have started here in Kodiak Alaska. Kodiak is a remote island in the middle of the gulf of Alaska. There are seven native villages around the island and Kodiak is the #2 fishing port in the United States. We also have the largest Coast Guard Base in the U.S. My company will be providing water taxi and freight transport logistics to the villages and many hunting and fishing lodges as well as remote properties around the island.

I would like a business card that isn't status quo, something that stands out, either in feel or appearance. I do like clean minimal designs but it needs to have the necessary contact info on it.

Target Market(s)

remote lodge / property owners, residents of the many villages around Kodiak and any one wanting to enjoy the great outdoors of Kodiak Alaska

Industry/Entity Type

Business

Contact Information for Business Card

I like clean simple designs that aren't cluttered but still provide the necessary information

Colors
0255a3
3277b5
33a4d5
9bcb3c
add136
fbed22
ffc214
f78f20
f37122

Requirements
Must have
• logo and contact info
• Captain Mason Elwick
• www.marrowbyferryline.com
• mason@marrowbyferryline.com

```html
<!DOCTYPE html>
<html lang="en">
<head>
<meta charset="utf-8">
<title>Marrowby Water Taxi and Transport — Business Card</title>
<link href="https://fonts.googleapis.com/css2?family=Open+Sans:wght@400;600;700;800&display=swap" rel="stylesheet">
<style>
  :root {
    --navy: #0255a3;
    --blue: #3277b5;
    --sky: #33a4d5;
    --deep: #0d3f8f;
    --orange: #f78f20;
    --sun: #ffc214;
    --ink: #2a3340;
    --paper: #ffffff;
    --backdrop: #e9ecef;
  }
  * { margin: 0; padding: 0; box-sizing: border-box; }
  html, body { width: 1200px; height: 913px; overflow: hidden; }
  body {
    background: var(--backdrop);
    font-family: "Open Sans", Arial, sans-serif;
    position: relative;
  }
  .card {
    position: absolute;
    top: 302px;
    width: 540px;
    height: 309px;
    overflow: hidden;
    box-shadow: 0 6px 18px rgba(0,0,0,.18);
  }
  .card--front { left: 45px; background: var(--paper); }
  .card--back {
    left: 615px;
    background: linear-gradient(160deg, #3d93d8 0%, var(--navy) 55%, var(--deep) 100%);
  }
  .card svg.bands { position: absolute; inset: 0; }

  .logo-art {
    position: absolute;
    left: 34px; top: 34px;
    width: 190px; height: 100px;
    border-radius: 6px;
    background: linear-gradient(180deg, #fde1a6 0%, #9fd0ec 45%, #5b9ccf 100%);
  }
  .brand-name {
    position: absolute;
    left: 34px; top: 140px;
    width: 230px;
    color: var(--navy);
    font-weight: 700;
    font-size: 15px;
    line-height: 1.25;
  }
  .holder-name {
    position: absolute;
    right: 26px; top: 112px;
    color: var(--navy);
    font-weight: 700;
    font-size: 21px;
    letter-spacing: .2px;
  }
  .contact {
    position: absolute;
    left: 34px; top: 228px;
    list-style: none;
    color: var(--ink);
    font-size: 13.5px;
    line-height: 19px;
  }
  .contact li { display: flex; align-items: center; gap: 8px; }
  .contact svg { width: 12px; height: 12px; flex: none; }

  .emblem-art {
    position: absolute;
    left: 160px; top: 70px;
    width: 230px; height: 175px;
    border-radius: 8px;
    background: radial-gradient(ellipse at 55% 40%, #c9d2da 0%, #8fc4e6 45%, rgba(51,164,213,.25) 100%);
  }
</style>
</head>
<body>

  <section class="card card--front" aria-label="Business card front">
    <svg class="bands" width="540" height="309" viewBox="0 0 540 309" aria-hidden="true">
      <polyline points="34,215 250,215 292,140 540,140" fill="none" stroke="var(--navy)" stroke-width="1.4"/>
      <polygon points="300,262 540,196 540,309 300,309" fill="var(--sky)"/>
      <polygon points="0,285 250,285 262,262 340,262 360,309 0,309" fill="var(--navy)"/>
    </svg>

    <div class="logo-art" role="img" aria-label="Company emblem: mountains, setting sun and ferry boat on waves"></div>
    <p class="brand-name">Marrowby<br>Water Taxi and Transport</p>

    <h1 class="holder-name">Captain Mason Elwick</h1>

    <ul class="contact">
      <li>
        <svg viewBox="0 0 12 12" aria-hidden="true"><rect x="0.6" y="2" width="10.8" height="8" fill="none" stroke="var(--orange)" stroke-width="1.2"/><polyline points="0.6,2 6,7 11.4,2" fill="none" stroke="var(--orange)" stroke-width="1.2"/></svg>
        mason@marrowbyferryline.com
      </li>
      <li>
        <svg viewBox="0 0 12 12" aria-hidden="true"><circle cx="6" cy="6" r="5.3" fill="none" stroke="var(--orange)" stroke-width="1.2"/><line x1="0.7" y1="6" x2="11.3" y2="6" stroke="var(--orange)" stroke-width="1"/><ellipse cx="6" cy="6" rx="2.3" ry="5.3" fill="none" stroke="var(--orange)" stroke-width="1"/></svg>
        www.marrowbyferryline.com
      </li>
    </ul>
  </section>

  <section class="card card--back" aria-label="Business card back">
    <svg class="bands" width="540" height="309" viewBox="0 0 540 309" aria-hidden="true">
      <polygon points="440,95 540,70 540,250 440,275" fill="var(--orange)"/>
      <polygon points="0,309 440,275 540,250 540,268 460,309" fill="var(--sky)"/>
    </svg>
    <div class="emblem-art" role="img" aria-label="Large emblem: mountains, sun and ferry boat on waves"></div>
  </section>

</body>
</html>
```